Business cards in digital learning for freelancer

Hello, I need a business cards in french. I work in the Digital learning industries as freeelancer; I'm an expert in digital learning. I work in France. My customer are in the health industry, pharmaceutical industry, and training organization. I've got a logo. I offer three services: consulting, Design, and Training. In the consulting, I offers coaching to choose your digital learning tools and the digital learning strategy. For the Design, I product differents level of elearning like rapid-learning, elearning, micro-learning, video-learning. And for the training service, I've create training about pedagogy, digital learning management project, Digital learning design.
I join my Logo create in this platform. My universe is gamified. I like the life, and I'm very social. I want a card like I'm I. I love Art (painting), Europeen comics. I use in my visual support "permanent maker" font and caracters. I would like cards: elegant, modern, Top class. If you need any information, you can ask me.
thanks for ideas

Target Market(s)

in health industries and training organization for Training manager, instructor, human resources director

Contact Information for Business Card

Phone number : 06 71 38 95 14 , mail: bastiengolmier@quelmoto.fr, web: bastiengolmier.fr , Carrivo

Font styles to use
Sans Serif

Requirements
Must have
• Use my logo and write my 3 services (consulting, training, design)

```html
<!DOCTYPE html>
<html lang="fr">
<head>
<meta charset="utf-8">
<title>Golmier – Cartes de visite</title>
<link rel="stylesheet" href="https://fonts.googleapis.com/css2?family=Josefin+Sans:wght@400;600&family=Cinzel:wght@400&display=swap">
<style>
  :root {
    --backdrop: #121212;
    --card: #0a0a0a;
    --ink: #3c3c3c;
    --ink-soft: #2f2f2f;
    --rule: #4a4a4a;
    --mark: #1c1c1c;
  }
  * { margin: 0; padding: 0; box-sizing: border-box; }
  html, body { width: 1200px; height: 900px; overflow: hidden; background: var(--backdrop); }
  .canvas {
    width: 1200px; height: 900px;
    display: flex; flex-direction: column; align-items: center; justify-content: center;
    gap: 56px;
  }
  .card {
    width: 660px; height: 380px;
    background: var(--card);
    position: relative;
    box-shadow: 0 18px 40px rgba(0,0,0,.55);
  }
  .card--front { display: flex; flex-direction: column; align-items: center; justify-content: center; }
  .brand { display: flex; align-items: center; gap: 14px; }
  .brand__dot { width: 30px; height: 30px; border-radius: 50%; background: var(--mark); border: 0; }
  .brand__name {
    font-family: "Josefin Sans", sans-serif; font-weight: 600;
    color: var(--ink); letter-spacing: .08em; text-transform: uppercase;
  }
  .card--front .brand__name { font-size: 58px; }
  .tagline {
    font-family: "Cinzel", serif; color: var(--ink-soft);
    letter-spacing: .06em; margin-top: 10px;
  }
  .card--front .tagline { font-size: 21px; }

  .card--back { display: flex; align-items: center; padding: 0 48px; }
  .back__brand { width: 300px; display: flex; flex-direction: column; align-items: center; }
  .card--back .brand__name { font-size: 44px; }
  .card--back .brand__dot { width: 24px; height: 24px; }
  .card--back .tagline {
    font-size: 15px; display: flex; align-items: center; gap: 10px;
  }
  .tagline__line { width: 60px; height: 1px; background: var(--rule); }
  .divider { width: 1px; height: 190px; background: var(--rule); margin: 0 34px 0 22px; }
  .contact { font-family: "Josefin Sans", sans-serif; color: var(--ink); }
  .contact__name { font-size: 23px; letter-spacing: .03em; }
  .contact__role { font-size: 17px; margin-top: 4px; color: var(--ink-soft); }
  .contact__list { list-style: none; margin-top: 30px; }
  .contact__item { display: flex; align-items: center; gap: 10px; font-size: 18px; line-height: 28px; }
  .contact__icon { width: 18px; height: 18px; flex: none; }
</style>
</head>
<body>
<main class="canvas">
  <section class="card card--front" aria-label="Recto de la carte">
    <div class="brand">
      <span class="brand__dot"></span>
      <span class="brand__name">Golmier</span>
    </div>
    <p class="tagline">Consulting, Training, Design</p>
  </section>

  <section class="card card--back" aria-label="Verso de la carte">
    <div class="back__brand">
      <div class="brand">
        <span class="brand__dot"></span>
        <span class="brand__name">Golmier</span>
      </div>
      <p class="tagline"><span class="tagline__line"></span>Digital Learning<span class="tagline__line"></span></p>
    </div>
    <div class="divider"></div>
    <div class="contact">
      <p class="contact__name">Bastien Golmier</p>
      <p class="contact__role">Digital Learning consultant</p>
      <ul class="contact__list">
        <li class="contact__item">
          <svg class="contact__icon" viewBox="0 0 18 18" aria-hidden="true"><circle cx="9" cy="9" r="9" fill="#2a2a2a"/><path d="M6 5h2l1 2.5-1.2.8a5 5 0 0 0 2 2l.8-1.2L13 10v2a1 1 0 0 1-1 1A7 7 0 0 1 5 6a1 1 0 0 1 1-1z" fill="#0a0a0a"/></svg>
          06 71 38 95 14
        </li>
        <li class="contact__item">
          <svg class="contact__icon" viewBox="0 0 18 18" aria-hidden="true"><circle cx="9" cy="9" r="9" fill="#2a2a2a"/><rect x="4.5" y="6" width="9" height="6.5" fill="none" stroke="#0a0a0a" stroke-width="1.2"/><path d="M4.5 6l4.5 3.5L13.5 6" fill="none" stroke="#0a0a0a" stroke-width="1.2"/></svg>
          bastiengolmier@quelmoto.fr
        </li>
        <li class="contact__item">
          <svg class="contact__icon" viewBox="0 0 18 18" aria-hidden="true"><circle cx="9" cy="9" r="9" fill="#2a2a2a"/><circle cx="9" cy="9" r="4.5" fill="none" stroke="#0a0a0a" stroke-width="1.1"/><path d="M4.5 9h9M9 4.5c-2 2.5-2 6.5 0 9M9 4.5c2 2.5 2 6.5 0 9" fill="none" stroke="#0a0a0a" stroke-width="1"/></svg>
          bastiengolmier.fr
        </li>
        <li class="contact__item">
          <svg class="contact__icon" viewBox="0 0 18 18" aria-hidden="true"><circle cx="9" cy="9" r="9" fill="#2a2a2a"/></svg>
          /in/bastien-golmier-elearning
        </li>
      </ul>
    </div>
  </section>
</main>
</body>
</html>
```